New Business Card Design Project

We require a business card design for Vexalund, a newly established Indian company.
Our focus is on the development, manufacturing, and export of a diverse array of pharmaceutical products on a global scale. The card should convey a professional appearance, as our primary markets are in Africa, China, and Southeast Asian nations.
We envision a two-sided business card, with the reverse side dedicated to a logo set against a solid color or an elegantly designed pattern. The corners should be rounded. We would appreciate seeing both horizontal and vertical design options. We trust the designer to utilize their expertise in creating this design.

The content for the business card is included in the attached Word file.

Target Market(s)

Our primary markets are in Africa, China, and Southeast Asian, Latin America, Maldives, Sri Lanka

Industry/Entity Type

Pharmaceutical Manufacturing and Export

Contact Information for Business Card

Colors

Designer to choose colors to be used in the design.

Requirements
Must have
• The reverse side of the business card features solely the logo along with the tagline, "Care Beyond Borders."
Should not have
• The logo should not exceed two instances, encompassing both the front and back sides of the card.

```html
<!DOCTYPE html>
<html lang="en">
<head>
<meta charset="utf-8">
<title>Vexalund Business Card</title>
<link href="https://fonts.googleapis.com/css2?family=Montserrat:wght@500;700&family=Open+Sans:wght@400;600&display=swap" rel="stylesheet">
<style>
  :root {
    --stage: #222222;
    --brand-blue: #2ea7e0;
    --brand-coral: #f0604a;
    --paper: #ffffff;
    --ink: #1e1e1e;
  }
  * { margin: 0; padding: 0; box-sizing: border-box; }
  html, body { width: 1200px; height: 711px; overflow: hidden; background: var(--stage); }
  .canvas {
    position: relative; width: 1200px; height: 711px;
    display: flex; justify-content: center; align-items: center; gap: 60px;
  }
  .card {
    position: relative; width: 300px; height: 520px; overflow: hidden;
  }
  .card--back {
    background: var(--brand-blue);
    border-radius: 140px 0 140px 0;
  }
  .card--front {
    background: var(--paper);
    border-radius: 0 140px 0 140px;
  }
  .back-lockup {
    position: absolute; left: 50%; top: 50%;
    transform: translate(-50%, -50%) rotate(90deg);
    text-align: center; white-space: nowrap;
  }
  .back-lockup__name {
    font-family: "Montserrat", sans-serif; font-weight: 700;
    font-size: 58px; color: var(--paper); letter-spacing: 1px;
  }
  .back-lockup__tagline {
    font-family: "Open Sans", sans-serif; font-weight: 400;
    font-size: 15px; color: var(--paper); margin-top: 6px; letter-spacing: .5px;
  }
  .front-lockup {
    position: absolute; top: 70px; left: 0; right: 0;
    display: flex; justify-content: center; align-items: center; gap: 10px;
  }
  .front-lockup__dot {
    width: 16px; height: 16px; border-radius: 50%; background: var(--brand-blue);
  }
  .front-lockup__name {
    font-family: "Montserrat", sans-serif; font-weight: 700;
    font-size: 34px; color: var(--brand-blue);
  }
  .contact {
    position: absolute; left: 38px; right: 24px; bottom: 92px;
    font-family: "Open Sans", sans-serif; color: var(--ink);
  }
  .contact__person {
    font-family: "Montserrat", sans-serif; font-size: 24px; color: var(--brand-blue);
    white-space: nowrap;
  }
  .contact__first { font-weight: 700; }
  .contact__rest { font-weight: 500; }
  .contact__role { font-family: "Montserrat", sans-serif; font-weight: 500; font-size: 14px; margin: 2px 0 16px 100px; }
  .contact__address { font-size: 12px; line-height: 1.4; margin-bottom: 14px; }
  .contact__list { list-style: none; font-size: 12px; line-height: 1.7; }
  .contact__item { display: flex; align-items: center; gap: 8px; }
  .contact__icon { width: 13px; height: 13px; flex: none; }
</style>
</head>
<body>
<main class="canvas">
  <section class="card card--back" aria-label="Card reverse">
    <div class="back-lockup">
      <div class="back-lockup__name">Vexalund</div>
      <div class="back-lockup__tagline">Care Beyond Borders.</div>
    </div>
  </section>

  <section class="card card--front" aria-label="Card front">
    <div class="front-lockup">
      <span class="front-lockup__dot"></span>
      <span class="front-lockup__name">Vexalund</span>
    </div>

    <div class="contact">
      <p class="contact__person"><span class="contact__first">Rohan</span> <span class="contact__rest">K. Selvam</span></p>
      <p class="contact__role">CEO</p>
      <p class="contact__address">12, Kamal Nagar,<br>Nashik, 422001, India</p>
      <ul class="contact__list">
        <li class="contact__item">
          <svg class="contact__icon" viewBox="0 0 14 14" aria-hidden="true"><rect x="3" y="1" width="8" height="12" rx="1.5" fill="none" stroke="#f0604a" stroke-width="1.6"/></svg>
          +91 98765 43210
        </li>
        <li class="contact__item">
          <svg class="contact__icon" viewBox="0 0 14 14" aria-hidden="true"><circle cx="7" cy="7" r="6" fill="#2ea7e0"/><path d="M1 7h12M7 1c-3 3-3 9 0 12M7 1c3 3 3 9 0 12" stroke="#fff" stroke-width=".9" fill="none"/></svg>
          www.vexalund.com
        </li>
        <li class="contact__item">
          <svg class="contact__icon" viewBox="0 0 14 14" aria-hidden="true"><rect x="1" y="3" width="12" height="9" rx="1" fill="#f0604a"/><path d="M1.5 3.5L7 8l5.5-4.5" stroke="#fff" stroke-width="1.1" fill="none"/></svg>
          rselvam@vexalund.com
        </li>
      </ul>
    </div>
  </section>
</main>
</body>
</html>
```